Equine Podcast Cover Art Design

We need catchy cover art for a horse related podcast "Ride Onward Together"
Brief show description"
Whether you want to ride to experience horses, develop yourself to the next level as a horseman/horsewoman or ride to improve your physical and mental health, we are committed to helping you Ride Onward TogetherĀ®. Join us as we explore the nuance of equine management and sports as well as interview industry professionals to provide you with the knowledge necessary to be a better partner for your equine friends.
I have uploaded two existing logos we use for various purposes to give you an idea of existing style.
Target Market(s)
Horse owners and other equine professionals
Look and feel
Each slider illustrates characteristics of the customer's brand and the style your logo design should communicate.

```html
<!DOCTYPE html>
<html lang="en">
<head>
<meta charset="utf-8">
<title>Ride Onward Together — Podcast Cover</title>
<link rel="stylesheet" href="https://fonts.googleapis.com/css2?family=Alfa+Slab+One&family=Bebas+Neue&display=swap">
<style>
  :root {
    --ink: #111111;
    --panel-dark: #141414;
    --gold: #b5833a;
    --cream: #e6d8ae;
    --white: #ffffff;
    --photo-sky: #9fb6cc;
    --photo-gold: #b8862f;
    --photo-brown: #5a3418;
  }
  html, body {
    margin: 0;
    padding: 0;
    width: 1200px;
    height: 1200px;
    overflow: hidden;
    background: var(--ink);
  }
  .cover {
    position: relative;
    width: 1200px;
    height: 1200px;
    display: block;
  }
  .title-gold {
    font-family: "Alfa Slab One", serif;
    fill: var(--gold);
  }
  .title-big {
    font-family: "Bebas Neue", sans-serif;
    fill: var(--cream);
  }
  .registered {
    font-family: "Bebas Neue", sans-serif;
    fill: var(--cream);
  }
  .farm-name {
    font-family: "Alfa Slab One", serif;
    fill: var(--white);
  }
</style>
</head>
<body>
<svg class="cover" viewBox="0 0 1200 1200" xmlns="http://www.w3.org/2000/svg">
  <defs>
    <linearGradient id="rider-photo" x1="0" y1="0" x2="0.4" y2="1">
      <stop offset="0" stop-color="var(--photo-sky)"/>
      <stop offset="0.35" stop-color="var(--photo-gold)"/>
      <stop offset="0.75" stop-color="var(--photo-brown)"/>
      <stop offset="1" stop-color="#2a1a0e"/>
    </linearGradient>
    <linearGradient id="faded-photo" x1="0" y1="0" x2="1" y2="1">
      <stop offset="0" stop-color="#1d1d1d"/>
      <stop offset="1" stop-color="#0e0e0e"/>
    </linearGradient>
  </defs>

  <!-- dark left panel -->
  <rect class="panel-left" x="0" y="0" width="725" height="1200" fill="url(#faded-photo)"
        role="img" aria-label="Faded monochrome photo of a show jumper rider"/>

  <!-- photo on the right -->
  <rect class="panel-photo" x="725" y="0" width="475" height="1174" fill="url(#rider-photo)"
        role="img" aria-label="Photo of a rider on a bay horse clearing a jump at golden hour"/>
  <rect class="bottom-band" x="725" y="1174" width="475" height="26" fill="var(--ink)"/>

  <!-- headline -->
  <text class="title-gold" x="102" y="231" font-size="210" textLength="250" lengthAdjust="spacingAndGlyphs">Ride</text>
  <text class="title-gold" x="100" y="419" font-size="210" textLength="455" lengthAdjust="spacingAndGlyphs">Onward</text>
  <text class="title-big" x="98" y="916" font-size="560" textLength="1010" lengthAdjust="spacingAndGlyphs">TOGETHER</text>
  <text class="registered" x="1108" y="570" font-size="64">®</text>

  <!-- farm mark -->
  <circle class="farm-badge" cx="175" cy="985" r="22" fill="none" stroke="var(--white)" stroke-width="3"/>
  <text class="farm-name" x="175" y="1045" font-size="22" text-anchor="middle">EVERGREEN</text>
  <text class="farm-name" x="175" y="1074" font-size="22" text-anchor="middle">PADDOCK FARM</text>
</svg>
</body>
</html>
```